Flyer to advertise gutter cleaning throughout the Autumn and winter monthss

I need a new flyer to advertise gutter and driveway cleaning, roof and gutter repairs.

I am an experienced licensed Plumber and Gasfitter looking to broaden my scope of work to gutter cleaning. I am experienced in cleaning gutter and live in a area with large gum trees. I wont something that's clear, eye catching but not too busy.

Flyer requirements: Free roof inspection - no obligation. Gutter Cleaning from $199. Pictures of men using blower or hands to clean roof gutters (no obvious faces) to be included. Australian looking houses.

A mention that 'All general plumbing maintenance' is offered as other services but not too much wording about this as the target is for gutter cleaning.

Phone number: 0427 385 912 (in this format)
Business Name: Larkvale Plumbing & Gasfitting
License: 3175420
ABN: 71364058227
Web: http://larkvaleplumbing.example.site/

Target Market(s)

Elderly - busy working class

Industry/Entity Type

Plumber

Font styles to use
Sans Serif

Colors
0355a3
fbed22
ec1f27
f78f20

Requirements
Must have
• Roof Gutter Cleaning pictures
• Men in protective clothing if possible
Nice to have
• More information:
• Prevent against flooding, mold, rust, rotting and corrosion now!
• Gutter Cleaning Services
• • Remove leaves, sticks, and other debris
• • Clear away clogs
• • Test your downpipes
• • Pinpoint any gutter issues
• • Repair gutter
• With regular service, you can count on your property to be well-protected no matter what the forecast!
Should not have
• Houses that don't look Australian

```html
<!DOCTYPE html>
<html lang="en">
<head>
<meta charset="utf-8">
<title>Larkvale Plumbing &amp; Gasfitting – Gutter and Driveway Cleaning</title>
<link rel="stylesheet" href="https://fonts.googleapis.com/css2?family=Open+Sans:ital,wght@0,400;0,600;0,700;0,800;1,400&family=Kaushan+Script&display=swap">
<style>
  :root {
    --navy: #252062;
    --red: #ec1f47;
    --red-deep: #e8153a;
    --yellow: #e6dc1f;
    --teal: #0f7876;
    --grey: #e3e3e1;
    --ink: #111111;
    --white: #ffffff;
  }
  * { box-sizing: border-box; margin: 0; padding: 0; }
  html, body { width: 943px; height: 1200px; overflow: hidden; background: #f2f2f2; }
  .flyer {
    position: relative; width: 943px; height: 1200px; overflow: hidden;
    background: var(--grey); font-family: "Open Sans", sans-serif;
  }
  .hero-panel { position: absolute; left: 0; top: 0; width: 577px; height: 528px; background: var(--navy); }
  .brand { position: absolute; left: 52px; top: 62px; display: flex; align-items: center; gap: 12px; }
  .brand-dot { width: 34px; height: 34px; border-radius: 50%; background: var(--red); }
  .brand-name { color: var(--white); font-weight: 700; font-size: 17px; letter-spacing: -0.2px; }
  .accent-rule { position: absolute; left: 52px; top: 156px; width: 155px; height: 6px; background: var(--red); }
  .headline {
    position: absolute; left: 48px; top: 172px; color: var(--white);
    font-weight: 800; font-size: 68px; line-height: 73px; letter-spacing: -0.5px; text-transform: uppercase;
  }
  .price { position: absolute; left: 50px; top: 384px; display: flex; align-items: baseline; gap: 14px; }
  .price-from { font-family: "Kaushan Script", cursive; color: var(--white); font-size: 60px; }
  .price-amount { color: var(--yellow); font-weight: 800; font-size: 92px; letter-spacing: -2px; }
  .other-services {
    position: absolute; left: 0; top: 528px; width: 577px; height: 166px;
    background: linear-gradient(90deg, var(--red-deep), var(--red));
    padding: 30px 0 0 56px; color: var(--white);
    font-style: italic; font-size: 15.5px; line-height: 22.7px;
  }
  .photo { position: absolute; }
  .photo-roof { left: 577px; top: 0; width: 366px; height: 803px;
    background: linear-gradient(170deg, #c7d2de 0%, #5d6c84 30%, #3d4a62 55%, #b4b07a 78%, #e3c640 90%, #f1f1ee 100%); }
  .photo-hands { left: 531px; top: 813px; width: 412px; height: 155px;
    background: linear-gradient(110deg, #b07a5a 0%, #c9a37c 35%, #7b6f62 65%, #6d6a66 100%); }
  .photo-pressure { left: 531px; top: 978px; width: 412px; height: 155px;
    background: linear-gradient(180deg, #4c6530 0%, #5f7a3d 30%, #8e5a4e 55%, #a8766a 100%); }
  .legal-strip {
    position: absolute; left: 577px; top: 1142px; width: 366px; height: 58px;
    background: linear-gradient(90deg, #4a4a4a, #6a6a6a);
    color: var(--white); font-size: 13px; display: flex; align-items: center; justify-content: flex-end; padding-right: 18px;
  }
  .seal {
    position: absolute; left: 428px; top: 470px; width: 282px; height: 282px;
    border-radius: 50%; background: var(--teal);
  }
  .services { position: absolute; left: 70px; top: 750px; }
  .services-title { font-weight: 700; font-size: 37px; color: var(--ink); letter-spacing: 0.3px; }
  .services-list { list-style: none; margin-top: 2px; }
  .services-list li { display: flex; align-items: center; gap: 8px; font-size: 24px; line-height: 38px; color: var(--ink); }
  .services-list svg { width: 16px; height: 16px; }
  .contact { position: absolute; left: 0; top: 994px; width: 490px; text-align: center; }
  .contact-cta { color: var(--navy); font-weight: 800; font-size: 28px; line-height: 31px; }
  .contact-phone { color: var(--red); font-weight: 800; font-size: 58px; line-height: 66px; letter-spacing: -0.5px; margin-top: 6px; }
  .contact-web { color: var(--navy); font-weight: 800; font-size: 15.5px; margin-top: 0; }
</style>
</head>
<body>
<main class="flyer">
  <section class="hero-panel">
    <div class="brand"><span class="brand-dot"></span><span class="brand-name">Larkvale Plumbing &amp; Gasfitting</span></div>
    <div class="accent-rule"></div>
    <h1 class="headline">Gutter and<br>Driveway<br>Cleaning</h1>
    <div class="price"><span class="price-from">From</span><span class="price-amount">$199</span></div>
  </section>

  <section class="other-services">
    Plumbing Maintenance, Sewer &amp; Stormwater<br>
    High Pressure Cleaning, Hot Water Systems<br>
    Renovations, Blocked Drains - Jet Rodding<br>
    TMV Testing, Backflow Testing &amp; Prevention<br>
    Gasfitting and Appliance Installation
  </section>

  <div class="photo photo-roof" role="img" aria-label="Close-up of roof shingles above a gutter filled with autumn leaves"></div>
  <div class="photo photo-hands" role="img" aria-label="Gloved hand scooping dry leaves out of a roof gutter"></div>
  <div class="photo photo-pressure" role="img" aria-label="Worker in overalls pressure washing a paved driveway"></div>

  <div class="seal" role="img" aria-label="Round all work guaranteed seal"></div>

  <section class="services">
    <h2 class="services-title">OUR SERVICES</h2>
    <ul class="services-list">
      <li><svg viewBox="0 0 16 16"><path d="M2 8 L6 13 L14 3" fill="none" stroke="var(--red)" stroke-width="2.2"/></svg>Gutter cleaning</li>
      <li><svg viewBox="0 0 16 16"><path d="M2 8 L6 13 L14 3" fill="none" stroke="var(--red)" stroke-width="2.2"/></svg>Driveway cleaning</li>
      <li><svg viewBox="0 0 16 16"><path d="M2 8 L6 13 L14 3" fill="none" stroke="var(--red)" stroke-width="2.2"/></svg>Roof repairs</li>
      <li><svg viewBox="0 0 16 16"><path d="M2 8 L6 13 L14 3" fill="none" stroke="var(--red)" stroke-width="2.2"/></svg>Gutter repairs</li>
    </ul>
  </section>

  <section class="contact">
    <p class="contact-cta">CALL FOR FREE<br>ROOF INSPECTION</p>
    <p class="contact-phone">0427 385 912</p>
    <p class="contact-web">www.larkvaleplumbing.example.site</p>
  </section>

  <footer class="legal-strip">License: 3175420 | ABN: 71364058227</footer>
</main>
</body>
</html>
```